Construction business card

I need a new business card, they can connect with my logo, brand.
What we do is residential house , design and build
I like: Navy blue / black
I attached our logo, brand,
and, some idea for business card.

```html
<!DOCTYPE html>
<html lang="en">
<head>
<meta charset="utf-8">
<title>Harwell Building Group – Business Card</title>
<link href="https://fonts.googleapis.com/css2?family=Arimo:wght@400;700&display=swap" rel="stylesheet">
<style>
  :root {
    --stage: #3a3a3c;
    --card-blue: #3b88c9;
    --ink-white: #ffffff;
    --ink-soft: rgba(255,255,255,0.92);
  }
  * { box-sizing: border-box; margin: 0; padding: 0; }
  html, body {
    width: 1200px; height: 875px; overflow: hidden;
    background: var(--stage);
    font-family: "Arimo", Arial, sans-serif;
  }
  .canvas {
    position: relative; width: 1200px; height: 875px;
    display: flex; align-items: center; justify-content: center; gap: 44px;
  }
  .card {
    position: relative; width: 540px; height: 309px;
    background: var(--card-blue);
    border-radius: 18px;
    color: var(--ink-white);
    box-shadow: 0 10px 30px rgba(0,0,0,0.35);
    overflow: hidden;
  }
  /* Front */
  .card--front { display: flex; align-items: center; justify-content: center; }
  .brand-mark {
    display: flex; align-items: center; gap: 12px;
    font-weight: 700; color: var(--ink-white);
    text-transform: uppercase; letter-spacing: 0.04em;
  }
  .brand-mark__square { background: var(--ink-white); flex: none; }
  .card--front .brand-mark { font-size: 34px; line-height: 1.05; }
  .card--front .brand-mark__square { width: 30px; height: 30px; }
  .brand-mark__name { display: block; }

  /* Back */
  .holder {
    position: absolute; top: 34px; right: 36px; text-align: right;
  }
  .holder__name { font-size: 20px; font-weight: 700; letter-spacing: 0.02em; }
  .holder__role { font-size: 13px; font-weight: 400; margin-top: 3px; color: var(--ink-soft); }

  .card--back .brand-mark {
    position: absolute; left: 36px; top: 104px; font-size: 18px;
  }
  .card--back .brand-mark__square { width: 18px; height: 18px; }

  .contact {
    position: absolute; left: 36px; bottom: 30px;
    font-size: 12.5px; line-height: 1.45; color: var(--ink-soft);
    list-style: none;
  }
  .contact__address { margin-bottom: 8px; }
  .contact__item { display: flex; align-items: center; gap: 8px; }
  .contact__icon { width: 12px; height: 12px; flex: none; }
</style>
</head>
<body>
<main class="canvas">

  <section class="card card--front" aria-label="Business card front">
    <div class="brand-mark">
      <span class="brand-mark__square" aria-hidden="true"></span>
      <span class="brand-mark__name">Harwell<br>Building Group</span>
    </div>
  </section>

  <section class="card card--back" aria-label="Business card back">
    <div class="holder">
      <p class="holder__name">DALEN WHITFORD</p>
      <p class="holder__role">CEO/Founder</p>
    </div>

    <div class="brand-mark">
      <span class="brand-mark__square" aria-hidden="true"></span>
      <span class="brand-mark__name">Harwell<br>Building Group</span>
    </div>

    <ul class="contact">
      <li class="contact__address">48 Ferncourt Rd,<br>Glenhaven, VIC 3190</li>
      <li class="contact__item">
        <svg class="contact__icon" viewBox="0 0 24 24" aria-hidden="true"><path fill="#fff" d="M6.6 10.8a15 15 0 0 0 6.6 6.6l2.2-2.2c.3-.3.7-.4 1-.2 1.1.4 2.3.6 3.6.6.6 0 1 .4 1 1V20c0 .6-.4 1-1 1A17 17 0 0 1 3 4c0-.6.4-1 1-1h3.5c.6 0 1 .4 1 1 0 1.3.2 2.5.6 3.6.1.3 0 .7-.2 1z"/></svg>
        <span>0400 555 018</span>
      </li>
      <li class="contact__item">
        <svg class="contact__icon" viewBox="0 0 24 24" aria-hidden="true"><path fill="#fff" d="M3 5h18v14H3z"/><path d="M3 5l9 7 9-7" fill="none" stroke="#3b88c9" stroke-width="2"/></svg>
        <span>info@harwellbuild.com.au</span>
      </li>
      <li class="contact__item">
        <svg class="contact__icon" viewBox="0 0 24 24" aria-hidden="true"><circle cx="12" cy="12" r="10" fill="none" stroke="#fff" stroke-width="2"/><path d="M2 12h20M12 2c3 3 3 17 0 20M12 2c-3 3-3 17 0 20" fill="none" stroke="#fff" stroke-width="1.6"/></svg>
        <span>harwellbuild.com.au</span>
      </li>
    </ul>
  </section>

</main>
</body>
</html>
```